Webdesign für Zahnarztpraxis
Zielgruppe
Zahnarztpraxis
Aufgabenstellung
- Klares und übersichtliches Desgin
- Nicht zu verspielt
- Informativ
- Leichte Naviagtion
- Das Design der alten Webseite soll NICHT kopiert werden
- Die Farben Blau und Grün aus dem Logo sollen sich wiederfinden
- Designbeispiele, die dem Kunden gefallen sind https://www.falkmann-ostrup-zahnarztpraxis.de/ und https://www.zahvilkorn.de/

```html
<!DOCTYPE html>
<html lang="de">
<head>
<meta charset="utf-8">
<title>Zahnwerk – Praxis & Dentallabor in Grünfelden</title>
<link href="https://fonts.googleapis.com/css2?family=Poppins:wght@300;400;500;600&display=swap" rel="stylesheet">
<style>
:root{
  --blue:#1e9ad6;
  --blue-dark:#1786c2;
  --green:#6cb33f;
  --text:#2b2b2b;
  --muted:#666;
  --card:#eaf7fd;
  --grey-bg:#f2f2f2;
  --light-bg:#eaf6fd;
  --white:#fff;
}
*{margin:0;padding:0;box-sizing:border-box}
html,body{width:1200px;height:5212px;overflow:hidden}
body{font-family:'Poppins',sans-serif;color:var(--text);background:var(--white);position:relative}
.abs{position:absolute}
.btn-grad{background:linear-gradient(90deg,var(--blue),var(--green));color:#fff;border-radius:30px;display:flex;align-items:center;justify-content:center;font-size:13px}

/* header */
.site-header{position:absolute;top:0;left:0;width:1200px;height:80px;background:#fff}
.brand{position:absolute;left:80px;top:22px;display:flex;align-items:center;gap:10px;font-size:26px;font-weight:500;color:var(--blue)}
.brand-dot{width:26px;height:26px;border-radius:50%;background:var(--green)}
.main-nav{position:absolute;left:280px;top:31px;display:flex;gap:22px;font-size:13px;color:#555}
.header-cta{left:968px;top:20px;width:168px;height:42px}

/* hero */
.hero{position:absolute;top:80px;left:0;width:1200px;height:818px;background:linear-gradient(135deg,#1a9ad9 0%,#2aa0c8 40%,#4fae6e 70%,#6cb33f 100%)}
.hero h1{position:absolute;top:56px;width:100%;text-align:center;color:#fff;font-weight:500;font-size:56px;line-height:60px}
.hero p{position:absolute;top:188px;width:100%;text-align:center;color:#fff;font-size:20px;line-height:26px;font-weight:300}
.hero-btn{left:518px;top:264px;width:164px;height:40px;background:#fff;border-radius:20px;color:#555;font-size:13px;display:flex;align-items:center;justify-content:center}
.hero-photo{left:0;top:320px;width:1200px;height:498px;background:linear-gradient(180deg,rgba(255,255,255,.1),rgba(255,255,255,.45));}

/* services */
.services h2{left:67px;top:1022px;font-size:36px;font-weight:500;color:var(--blue)}
.services h2 span{color:var(--green)}
.service-card{position:absolute;width:320px;height:81px;background:var(--card);border-radius:10px;display:flex;align-items:center;padding-left:20px;gap:18px;font-size:15px;color:#333}
.service-card svg{width:38px;height:38px;flex:none}
.services-photo{left:399px;top:1006px;width:405px;height:630px;border-radius:14px;background:linear-gradient(160deg,#f2ece4,#e9d9cc 45%,#e69ab0 80%,#d27c9a)}

/* labor */
.labor{position:absolute;top:1745px;left:0;width:1200px;height:715px;background:var(--grey-bg)}
.labor h2{left:90px;top:82px;font-size:40px;font-weight:500;color:var(--blue)}
.labor p{left:90px;top:138px;font-size:13px;line-height:20px;color:#555;width:220px}
.labor-photo-a{left:548px;top:79px;width:587px;height:421px;border-radius:18px;background:linear-gradient(135deg,#c8e4e2,#dff0ec 50%,#a9d4c6)}
.labor-frame{left:67px;top:277px;width:558px;height:382px;background:#fff;border-radius:0 0 0 18px}
.labor-photo-b{left:67px;top:303px;width:534px;height:336px;border-radius:18px;background:linear-gradient(135deg,#a9d2c9,#e2f0ee 50%,#9cc8ae)}
.labor-btn{left:945px;top:595px;width:184px;height:46px}

/* team */
.team h2{left:0;top:2568px;width:1200px;text-align:center;font-size:42px;font-weight:500;color:var(--blue)}
.team h2 span{color:var(--green)}
.member{position:absolute;top:2666px;width:221px;text-align:center}
.member .photo{width:221px;height:220px;border-radius:6px}
.member h3{margin-top:18px;font-size:15px;font-weight:500;line-height:20px}
.member p{margin-top:10px;font-size:10px;line-height:15px;color:#444}
.arrow-plain{top:2826px;width:22px;height:34px}
.team-btn{left:510px;top:3074px;width:178px;height:45px}

/* testimonials */
.review{position:absolute;top:3224px;width:282px;height:225px;background:#fff;border-radius:10px;box-shadow:0 2px 12px rgba(0,0,0,.08);padding:22px 20px}
.review .who{display:flex;align-items:center;gap:14px;font-size:10px;font-weight:500}
.review .avatar{width:28px;height:28px;border-radius:50%;background:#d9dde2}
.review .quote{margin-top:26px;font-size:10px;line-height:14px;color:#333}
.review .stars{position:absolute;left:20px;bottom:26px;display:flex;gap:8px}
.review .marks{position:absolute;right:20px;bottom:28px;display:flex;gap:4px}
.review .marks i{width:16px;height:16px;border-radius:50%;background:#e3e3e3}
.arrow-round{top:3316px;width:44px;height:44px;border-radius:50%;background:linear-gradient(135deg,var(--blue),var(--green));display:flex;align-items:center;justify-content:center}

/* hours */
.hours-band{position:absolute;top:3560px;left:0;width:1200px;height:1075px;background:var(--light-bg)}
.hours-photo{left:65px;top:3649px;width:538px;height:500px;border-radius:18px;background:linear-gradient(150deg,#eef1f1,#d8dde0 40%,#3c5166 75%,#c9b190)}
.hours-card{left:625px;top:3649px;width:510px;height:500px;background:#fff;border-radius:18px;padding:18px 15px;font-size:12.5px;line-height:19px;color:#333}
.hours-card h2{font-size:38px;font-weight:500;color:var(--blue);line-height:46px;margin-bottom:12px}
.hours-card h3{font-size:19px;font-weight:500;color:var(--blue);line-height:26px;margin:4px 0}
.hours-card table{border-collapse:collapse}
.hours-card td{padding:0 14px 0 0;vertical-align:top}
.hours-card .gap{margin-top:14px}
.kids-photo{left:65px;top:4180px;width:1070px;height:354px;border-radius:18px;background:linear-gradient(90deg,#e9c980,#f3ecdd 35%,#a8d47a 52%,#f0e4df 70%,#e8d4cc)}

/* footer */
.site-footer{position:absolute;top:4635px;left:0;width:1200px;height:577px;background:linear-gradient(120deg,#6cb33f 0%,#3fa59a 45%,#1e9ad6 100%);color:#fff}
.foot-brand{left:130px;top:145px;display:flex;align-items:center;gap:12px;font-size:40px;font-weight:500}
.foot-brand .brand-dot{width:40px;height:40px;background:#fff}
.socials{left:138px;top:263px;display:flex;gap:36px}
.socials span{width:44px;height:44px;border:1.5px solid #fff;border-radius:50%}
.foot-col h4{font-size:17px;font-weight:500;margin-bottom:18px}
.foot-col li{list-style:none;font-size:12.5px;line-height:29px}
.contact-row{display:flex;gap:12px;font-size:12.5px;line-height:18px;margin-bottom:22px}
.contact-row svg{flex:none;margin-top:2px}
.foot-line{left:65px;top:399px;width:1070px;height:1px;background:rgba(255,255,255,.55)}
.copyright{left:0;top:455px;width:1200px;text-align:center;font-size:12px}
</style>
</head>
<body>
<svg width="0" height="0" style="position:absolute">
  <defs>
    <symbol id="tooth" viewBox="0 0 40 40"><path d="M10 6c-5 0-7 5-6 10 1 4 3 6 4 11 1 5 2 9 4 9s3-6 5-10c1-2 3-2 4 0 2 4 3 10 5 10s3-4 4-9c1-5 3-7 4-11 1-5-1-10-6-10-4 0-6 2-9 2s-5-2-9-2z" fill="none" stroke="#1e9ad6" stroke-width="1.6" stroke-linejoin="round"/></symbol>
    <symbol id="star" viewBox="0 0 20 20"><path d="M10 1l2.7 5.8 6.3.7-4.7 4.3 1.3 6.2L10 14.9 4.4 18l1.3-6.2L1 7.5l6.3-.7z" fill="#2aa7a0"/></symbol>
  </defs>
</svg>

<header class="site-header">
  <div class="brand"><span class="brand-dot"></span>Zahnwerk</div>
  <nav class="main-nav"><span>Startseite</span><span>Unsere Praxis</span><span>Eigenes Praxislabor</span><span>Unsere Leistungen</span><span>Unser Team</span><span>Anfahrt</span></nav>
  <div class="abs btn-grad header-cta">Kontaktieren Sie uns</div>
</header>

<section class="hero">
  <h1>Praxis &amp; Dentallabor in<br>Grünfelden.</h1>
  <p>Prävention und Individualprophylaxe in jeder Altersgruppe!<br>Zahnärztin spricht auch fließend Englisch.</p>
  <div class="abs hero-btn">Termin Buchen</div>
  <div class="abs hero-photo" role="img" aria-label="Gruppenfoto des Praxisteams in weißen Jacken"></div>
</section>

<section class="services">
  <h2 class="abs">Unsere <span>Leistungen</span></h2>
  <div class="service-card" style="left:67px;top:1117px"><svg><use href="#tooth"/></svg>Zahnärztliche Diagnostik</div>
  <div class="service-card" style="left:67px;top:1227px"><svg><use href="#tooth"/></svg>Individualprophylaxe</div>
  <div class="service-card" style="left:67px;top:1336px"><svg><use href="#tooth"/></svg>Professionelle Zahnreinigung</div>
  <div class="service-card" style="left:67px;top:1445px"><svg><use href="#tooth"/></svg>Konservierende Zahnheilkunde</div>
  <div class="service-card" style="left:67px;top:1554px"><svg><use href="#tooth"/></svg>Zahnärztliche Prothetik</div>
  <div class="abs services-photo" role="img" aria-label="Zahnärztin behandelt ein lachendes Mädchen"></div>
  <div class="service-card" style="left:814px;top:1006px"><svg><use href="#tooth"/></svg>Kieferorthopädie</div>
  <div class="service-card" style="left:814px;top:1116px"><svg><use href="#tooth"/></svg>Chirurgische Zahnheilkunde</div>
  <div class="service-card" style="left:814px;top:1225px"><svg><use href="#tooth"/></svg>Ästhetische Zahnheilkunde</div>
  <div class="service-card" style="left:814px;top:1335px"><svg><use href="#tooth"/></svg>Ganzheitliche Zahnheilkunde</div>
  <div class="service-card" style="left:814px;top:1444px"><svg><use href="#tooth"/></svg>Kinderzahnheilkunde</div>
  <div class="service-card" style="left:814px;top:1554px"><svg><use href="#tooth"/></svg>Bioverträglicher Zahnersatz</div>
</section>

<section class="labor">
  <h2 class="abs">Praxislabor</h2>
  <p class="abs">Unsere Praxis verfügt über ein eigenes Praxislabor.</p>
  <div class="abs labor-photo-a" role="img" aria-label="Behandlungszimmer mit Zahnarztstuhl und Fenster"></div>
  <div class="abs labor-frame"></div>
  <div class="abs labor-photo-b" role="img" aria-label="Behandlungsraum mit Monitor und Pflanze"></div>
  <div class="abs btn-grad labor-btn">Kontaktieren Sie uns</div>
</section>

<section class="team">
  <h2 class="abs">Unser <span>Team</span></h2>
  <svg class="abs arrow-plain" style="left:70px" viewBox="0 0 22 34"><path d="M18 3L5 17l13 14" fill="none" stroke="#1e9ad6" stroke-width="3"/></svg>
  <svg class="abs arrow-plain" style="left:1106px" viewBox="0 0 22 34"><path d="M4 3l13 14L4 31" fill="none" stroke="#6cb33f" stroke-width="3"/></svg>
  <div class="member" style="left:121px"><div class="photo" role="img" aria-label="Porträt der Zahnärztin" style="background:linear-gradient(160deg,#eee,#d9c7b8)"></div><h3>Zahnärztin Marie Hollweg</h3><p>- 2004 Studienabschluss<br>- von 2005 bis 2015 in England tätig<br>- Behandlungsschwerpunkte: ästhetische, präventive Zahnheilkunde<br>Zahnaufhellung /Bleachingfeste,<br>kosmetische Zahnspangen</p></div>
  <div class="member" style="left:366px"><div class="photo" role="img" aria-label="Porträt der Praxismanagerin" style="background:linear-gradient(160deg,#eee,#e8c3c3)"></div><h3>Praxismanage<br>rin Sabine Kranich</h3><p>- Zahnmedizinische Fachassistentin<br>- seit 1989 in der Praxis<br>- Spezialisierung: Prophylaxe/<br>professionelle Zahnreinigung,<br>Abrechnung,<br>Praxisorganisation, Qualitätsmanagement</p></div>
  <div class="member" style="left:613px"><div class="photo" role="img" aria-label="Porträt der Zahntechnikerin" style="background:linear-gradient(160deg,#eee,#efe2a8)"></div><h3>Zahntechnikerin<br>Petra Lindner</h3><p>- 2002 Abschluss der<br>Ausbildung<br>- seit 2011 in unserer Praxis<br>- Spezialgebiete: Kronen- und<br>Brückentechnik</p></div>
  <div class="member" style="left:858px"><div class="photo" role="img" aria-label="Porträt der Assistentin" style="background:linear-gradient(160deg,#eee,#ecc8c8)"></div><h3>Assistentin Olga Berezin</h3><p>- Stuhlassistentin<br>- allg. Bürotätigkeiten</p></div>
  <div class="abs btn-grad team-btn">Termin buchen</div>

  <div class="abs arrow-round" style="left:89px"><svg width="14" height="18" viewBox="0 0 14 18"><path d="M10 2L3 9l7 7" fill="none" stroke="#fff" stroke-width="2.5"/></svg></div>
  <div class="abs arrow-round" style="left:1065px"><svg width="14" height="18" viewBox="0 0 14 18"><path d="M4 2l7 7-7 7" fill="none" stroke="#fff" stroke-width="2.5"/></svg></div>
  <div class="review" style="left:156px"><div class="who"><span class="avatar" role="img" aria-label="Profilbild"></span>Tom Reimers</div><p class="quote">„Ausgezeichneter Service“<br>Sehr freundliches Team, kurze Wartezeit und eine ruhige, gründliche Behandlung. Jederzeit gerne wieder.</p><div class="stars"><svg width="20" height="20"><use href="#star"/></svg><svg width="20" height="20"><use href="#star"/></svg><svg width="20" height="20"><use href="#star"/></svg><svg width="20" height="20"><use href="#star"/></svg><svg width="20" height="20"><use href="#star"/></svg></div><div class="marks"><i></i><i></i></div></div>
  <div class="review" style="left:466px"><div class="who"><span class="avatar" role="img" aria-label="Profilbild"></span>Tom Reimers</div><p class="quote">„Ausgezeichneter Service“<br>Sehr freundliches Team, kurze Wartezeit und eine ruhige, gründliche Behandlung. Jederzeit gerne wieder.</p><div class="stars"><svg width="20" height="20"><use href="#star"/></svg><svg width="20" height="20"><use href="#star"/></svg><svg width="20" height="20"><use href="#star"/></svg><svg width="20" height="20"><use href="#star"/></svg><svg width="20" height="20"><use href="#star"/></svg></div><div class="marks"><i></i><i></i></div></div>
  <div class="review" style="left:775px"><div class="who"><span class="avatar" role="img" aria-label="Profilbild"></span>Tom Reimers</div><p class="quote">„Ausgezeichneter Service“<br>Sehr freundliches Team, kurze Wartezeit und eine ruhige, gründliche Behandlung. Jederzeit gerne wieder.</p><div class="stars"><svg width="20" height="20"><use href="#star"/></svg><svg width="20" height="20"><use href="#star"/></svg><svg width="20" height="20"><use href="#star"/></svg><svg width="20" height="20"><use href="#star"/></svg><svg width="20" height="20"><use href="#star"/></svg></div><div class="marks"><i></i><i></i></div></div>
</section>

<section class="hours-band"></section>
<div class="abs hours-photo" role="img" aria-label="Helles Behandlungszimmer mit Zahnarztstuhl"></div>
<div class="abs hours-card">
  <h2>Unsere Öffnungszeiten:</h2>
  <table>
    <tr><td>Montag:</td><td>9:00 bis 13:00</td><td>Uhr</td><td>und&nbsp; 14:00 bis 19:00 Uhr</td></tr>
    <tr><td>Dienstag:</td><td>9:00 bis 13:00</td><td>Uhr</td><td>und&nbsp; 14:00 bis 19:00 Uhr</td></tr>
    <tr><td>Mittwoch:</td><td>9:00 bis 14:00</td><td>Uhr</td><td></td></tr>
  </table>
  <h3>Donnerstag: geschlossen</h3>
  <table><tr><td>Freitag:</td><td>9:00 bis 13:00</td><td>Uhr</td></tr></table>
  <div>… und nach Vereinbarung</div>
  <div class="gap">Informieren Sie sich bitte hier über Aktualisierungen auf unserem Praxis- Eintrag bei Ortsfinder.</div>
  <h3>Telefonzeiten:</h3>
  <div>Innerhalb dieser Zeiten sind wir für Sie telefonisch erreichbar:</div>
  <table class="gap">
    <tr><td>Montag:</td><td>9:00 bis 15:00</td><td>Uhr</td></tr>
    <tr><td>Dienstag:</td><td>9:00 bis 15:00</td><td>Uhr</td></tr>
    <tr><td>Mittwoch:</td><td>9:00 bis 12:00</td><td>Uhr</td></tr>
  </table>
  <div class="gap">In dringenden Fällen wenden Sie sich bitte an zahnärtlichen Notdienst. Link 'zur Notdienstsuche' https://www.zahnnotdienst-region.de/patienten/notdienstsuche/</div>
</div>
<div class="abs kids-photo" role="img" aria-label="Zahnärztin zeigt einem Kind das Zähneputzen an einem Plüschkrokodil"></div>

<footer class="site-footer">
  <div class="abs foot-brand"><span class="brand-dot"></span>Zahnwerk</div>
  <div class="abs socials"><span></span><span></span><span></span></div>
  <div class="abs foot-col" style="left:520px;top:108px"><h4>Schnelllink</h4><ul><li>Startseite</li><li>Unsere Praxis</li><li>Eigenes Praxislabor</li><li>Unsere Leistungen</li><li>Unser Team</li><li>Anfahrt</li></ul></div>
  <div class="abs foot-col" style="left:785px;top:108px"><h4>Kontakt</h4>
    <div class="contact-row"><svg width="16" height="18" viewBox="0 0 16 18"><path d="M8 17s6-6 6-10A6 6 0 0 0 2 7c0 4 6 10 6 10z" fill="none" stroke="#fff" stroke-width="1.5"/><circle cx="8" cy="7" r="2" fill="#fff"/></svg><div>Lindenweg 14<br>09876 Grünfelden</div></div>
    <div class="contact-row"><svg width="16" height="16" viewBox="0 0 16 16"><path d="M3 1l3 3-2 2c1 2 3 4 5 5l2-2 3 3-2 3C7 15 1 9 1 3z" fill="none" stroke="#fff" stroke-width="1.5"/></svg><div>Telefon: 03700-11245<br>Fax: 03700-11246</div></div>
    <div class="contact-row"><svg width="16" height="14" viewBox="0 0 16 14"><rect x="1" y="2" width="14" height="10" rx="1" fill="none" stroke="#fff" stroke-width="1.5"/><path d="M1 3l7 5 7-5" fill="none" stroke="#fff" stroke-width="1.5"/></svg><div>E-Mail: info@zahnarztpraxis-hollweg.de</div></div>
  </div>
  <div class="abs foot-line"></div>
  <div class="abs copyright">© 2008–2025 Praxis Hollweg Service GmbH. All rights reserved.</div>
</footer>
</body>
</html>
```